Oil Field Service company needs professional business cards

Looking to clean up our current company business cards and look a little more professional. Brenwick Casing Services is a US based company that services the oil field. We deal with engineers, managers and oil rigs....................................................................................................................................................................................................................................................................................................................................................................................................

Target Market(s)

Oil and Gas professionals

Industry/Entity Type

Oil And Gas

Contact Information for Business Card

See attached photo as example

Font styles to use
Sans Serif

Colors
ec1f27

Requirements
Must have
• Company Logo, Name, Title, Cell, Office, Fax, Email.
• See attached photo
Nice to have
• External CRT, Internal CRT, Casing Crews, Torque Turn, Laydown Machine
Should not have
• Do not introduce any new pictures and keep it professional looking

```html
<!DOCTYPE html>
<html lang="en">
<head>
<meta charset="utf-8">
<title>Brenwick Casing Services – Business Card</title>
<link rel="stylesheet" href="https://fonts.googleapis.com/css2?family=Oswald:wght@300;400;500&family=Roboto:wght@400&display=swap">
<style>
  :root {
    --brand-red: #d3201f;
    --brand-red-dark: #b81b1b;
    --slate: #3f5467;
    --ink: #3a3a3a;
    --muted: #6b6b6b;
    --card-white: #f7f7f7;
    --backdrop: #e4e4e4;
  }
  * { margin: 0; padding: 0; box-sizing: border-box; }
  html, body { width: 1200px; height: 576px; overflow: hidden; }
  body { background: var(--backdrop); position: relative; font-family: "Oswald", sans-serif; }

  .card {
    position: absolute;
    top: 138px;
    width: 485px;
    height: 294px;
    border-radius: 6px;
    overflow: hidden;
    box-shadow: 0 2px 4px rgba(0,0,0,0.18);
  }

  /* Front */
  .card-front {
    left: 81px;
    background: linear-gradient(180deg, var(--brand-red) 0%, var(--brand-red-dark) 100%);
    display: flex;
    flex-direction: column;
    align-items: center;
    justify-content: center;
    color: #fff;
  }
  .wordmark { font-family: "Oswald", sans-serif; font-weight: 500; text-align: center; line-height: 1; }
  .card-front .wordmark-name { font-size: 50px; letter-spacing: 2px; text-transform: uppercase; }
  .card-front .wordmark-tag { font-size: 15px; letter-spacing: 3px; text-transform: uppercase; margin-top: 10px; }

  /* Back */
  .card-back { left: 602px; background: var(--card-white); }
  .edge-band { position: absolute; left: 0; top: 0; bottom: 0; width: 40px; background: var(--brand-red); }
  .edge-rule { position: absolute; left: 40px; top: 0; bottom: 0; width: 6px; background: var(--slate); }

  .card-back .wordmark { position: absolute; right: 48px; top: 34px; color: var(--slate); }
  .card-back .wordmark-name { font-size: 36px; letter-spacing: 1.5px; text-transform: uppercase; }
  .card-back .wordmark-tag { font-size: 11px; letter-spacing: 2.4px; text-transform: uppercase; margin-top: 7px; }

  .person { position: absolute; left: 66px; top: 154px; }
  .person-name { font-family: "Oswald", sans-serif; font-weight: 400; font-size: 22px; color: var(--ink); line-height: 1.2; }
  .person-title { font-family: "Roboto", sans-serif; font-size: 11.5px; color: var(--muted); margin-top: 1px; }

  .contacts { position: absolute; top: 219px; left: 70px; display: flex; gap: 36px; }
  .contact-list { list-style: none; }
  .contact-list li {
    display: flex; align-items: center; gap: 8px;
    height: 16px;
    font-family: "Oswald", sans-serif; font-weight: 300;
    font-size: 12px; color: var(--ink);
  }
  .contact-list svg { width: 10px; height: 10px; fill: var(--brand-red); flex: none; }
</style>
</head>
<body>

<section class="card card-front" aria-label="Card front">
  <div class="wordmark">
    <div class="wordmark-name">Brenwick</div>
    <div class="wordmark-tag">Casing Services</div>
  </div>
</section>

<section class="card card-back" aria-label="Card back">
  <div class="edge-band"></div>
  <div class="edge-rule"></div>

  <div class="wordmark">
    <div class="wordmark-name">Brenwick</div>
    <div class="wordmark-tag">Casing Services</div>
  </div>

  <div class="person">
    <div class="person-name">Cody Harlan</div>
    <div class="person-title">Area Manager</div>
  </div>

  <div class="contacts">
    <ul class="contact-list">
      <li>
        <svg viewBox="0 0 10 10" aria-hidden="true"><path d="M2 0.5 L3.6 2.6 L2.7 3.6 Q3.6 5.8 6.4 7.3 L7.4 6.4 L9.5 8 L8.3 9.5 Q4.5 9.4 1.6 5.8 Q0.4 3.8 0.6 1.7 Z"/></svg>
        (555) 214-7300
      </li>
      <li>
        <svg viewBox="0 0 10 10" aria-hidden="true"><path d="M0.5 3.2 Q5 0.4 9.5 3.2 L8.6 4.4 L7 3.8 L7 3 Q5 2.4 3 3 L3 3.8 L1.4 4.4 Z M2.2 5 L7.8 5 L9 9.3 L1 9.3 Z"/></svg>
        (555) 318-6042
      </li>
      <li>
        <svg viewBox="0 0 10 10" aria-hidden="true"><path d="M2.5 0.5 H7.5 V3 H2.5 Z M0.5 3.6 H9.5 V7.5 H8 V6 H2 V7.5 H0.5 Z M2.8 6.8 H7.2 V9.5 H2.8 Z"/></svg>
        (555) 214-7391
      </li>
    </ul>
    <ul class="contact-list">
      <li>
        <svg viewBox="0 0 10 10" aria-hidden="true"><path d="M0.5 2 H9.5 L5 5.6 Z M0.5 3.2 L5 6.8 L9.5 3.2 V8.3 H0.5 Z"/></svg>
        codyharlan@brenwickcs.com
      </li>
      <li>
        <svg viewBox="0 0 10 10" aria-hidden="true"><path fill-rule="evenodd" d="M5 0.5 A4.5 4.5 0 1 1 4.99 0.5 Z M5 1.5 Q3.6 3 3.6 5 Q3.6 7 5 8.5 Q6.4 7 6.4 5 Q6.4 3 5 1.5 Z M1.6 4.5 H8.4 V5.5 H1.6 Z"/></svg>
        www.brenwickcs.com
      </li>
      <li>
        <svg viewBox="0 0 10 10" aria-hidden="true"><path fill-rule="evenodd" d="M5 0.3 A3.4 3.4 0 0 1 8.4 3.7 Q8.4 5.8 5 9.7 Q1.6 5.8 1.6 3.7 A3.4 3.4 0 0 1 5 0.3 Z M5 2.3 A1.4 1.4 0 1 0 5.01 2.3 Z"/></svg>
        Haskell Bend, OK 73890
      </li>
    </ul>
  </div>
</section>

</body>
</html>
```